Modern Verdell Tree Care Website

I need a website for a full service Tree Care company. The company provides tree pruning, tree removal, tree preservation, emergency services, stump grinding, and emergency tree services.

Target Market(s)

Customers that need tree services

Industry/Entity Type

Landscaping, Tree Services

Coding

Coded - Design and coding required

Number of Pages Required

5+ page

Font styles to use
Sans Serif

Requirements
Must have
• Good clean design that showcases the services the company provides.
Nice to have
• Services page; contact form, blog, home page, about page

```html
<!DOCTYPE html>
<html lang="en">
<head>
<meta charset="utf-8">
<title>Verdell Tree Care</title>
<link rel="stylesheet" href="https://fonts.googleapis.com/css2?family=Roboto:wght@400;500;700;900&family=Lato:wght@400;700&display=swap">
<style>
:root{
  --green:#8cc63f;
  --orange:#f9a937;
  --slate:#5f6e70;
  --ink:#111;
  --text:#333;
  --muted:#f5f5f5;
  --footer:#121312;
  --white:#fff;
}
*{box-sizing:border-box;margin:0;padding:0}
html,body{width:1200px;height:3687px;overflow:hidden}
body{position:relative;font-family:"Lato",sans-serif;color:var(--text);background:var(--white)}
.abs{position:absolute}
.head-font{font-family:"Roboto",sans-serif}

/* header */
.site-header{left:0;top:0;width:1200px;height:102px;background:var(--white)}
.brand{left:112px;top:30px;display:flex;align-items:center;gap:14px}
.brand-mark{width:40px;height:40px;background:var(--green)}
.brand-name{font-family:"Roboto",sans-serif;font-weight:700;font-size:30px;color:#5c6b6e;letter-spacing:1px}
.nav{top:42px;font-size:15px;color:#222}
.nav span{position:absolute;white-space:nowrap}

/* hero */
.hero{left:0;top:102px;width:1200px;height:585px;background:radial-gradient(ellipse at 40% 35%,#6d8a3a 0%,#3f5a22 45%,#2a2f1a 100%)}
.hero-title{left:0;top:148px;width:1200px;text-align:center;font-family:"Roboto",sans-serif;font-weight:700;font-size:100px;color:var(--white);line-height:115px}
.hero-title .mark{background:var(--green);padding:0 8px}
.hero-sub{left:0;top:290px;width:1200px;text-align:center;font-family:"Roboto",sans-serif;font-weight:700;font-size:27px;color:var(--white)}
.btn{display:flex;align-items:center;justify-content:center;font-family:"Roboto",sans-serif;font-weight:700;font-size:15px;text-transform:uppercase}
.btn-shop{left:428px;top:358px;width:136px;height:51px;background:var(--orange);color:var(--white)}
.btn-explore{left:583px;top:358px;width:187px;height:51px;background:var(--white);color:var(--ink)}

/* section heading with highlight */
.sec-title{font-family:"Roboto",sans-serif;font-weight:700;font-size:42px;color:var(--ink);line-height:48px;white-space:nowrap}
.sec-title .mark{background:var(--green);padding:0 14px 0 2px}

/* services */
.arrow{width:38px;height:38px;border-radius:50%;display:flex;align-items:center;justify-content:center}
.arrow-prev{left:1003px;top:777px;background:var(--orange)}
.arrow-next{left:1051px;top:777px;background:#e8e8e8}
.card{border-radius:10px;overflow:hidden}
.card-photo{border-radius:10px;display:flex;align-items:flex-end}
.card-label{font-family:"Roboto",sans-serif;font-weight:700;font-size:21px;color:var(--white);padding:0 0 26px 14px;white-space:nowrap}
.card-feature{left:444px;top:859px;width:311px;height:370px;background:var(--white);box-shadow:0 4px 22px rgba(0,0,0,.14);border-radius:10px}
.card-feature .img{position:absolute;left:11px;top:11px;width:289px;height:205px;border-radius:8px;background:linear-gradient(160deg,#6f9a45,#3e5a2c 60%,#5b4a36)}
.card-feature h3{position:absolute;left:20px;top:232px;font-family:"Roboto",sans-serif;font-weight:500;font-size:25px;color:var(--ink)}
.card-feature p{position:absolute;left:22px;top:266px;width:270px;font-size:12.5px;line-height:21px;color:#444}
.card-feature .more{position:absolute;left:24px;top:335px;font-size:12px;color:#3c5a3c;font-weight:700;display:flex;align-items:center;gap:4px}

/* about / why */
.blob{border-radius:48% 52% 44% 56% / 52% 42% 58% 48%}
.body-copy{font-size:15px;line-height:30px;color:#333}
.btn-slate{background:var(--slate);color:var(--white)}
.checklist{list-style:none}
.checklist li{display:flex;align-items:center;gap:9px;font-size:15px;height:34px;color:#333}

/* testimonials */
.testimonials{left:0;top:2300px;width:1200px;height:628px;background:var(--muted)}
.avatar{border-radius:50%;border:3px solid var(--white)}
.quote{left:190px;top:2583px;width:820px;text-align:center;font-size:15.5px;line-height:26px;color:#333}
.client-name{left:0;top:2724px;width:1200px;text-align:center;font-family:"Roboto",sans-serif;font-weight:500;font-size:22px;color:var(--ink)}
.client-role{left:0;top:2758px;width:1200px;text-align:center;font-size:13px;color:#333}

/* newsletter */
.newsletter{left:0;top:2928px;width:1200px;height:240px;background:var(--slate)}
.nl-title{left:115px;top:2990px;font-family:"Roboto",sans-serif;font-weight:700;font-size:34px;color:var(--white)}
.nl-text{left:117px;top:3050px;width:450px;font-size:15px;line-height:24px;color:var(--white)}
.nl-input{left:677px;top:2989px;width:414px;height:54px;border:1.5px solid var(--white);color:var(--white);font-size:15px;padding:17px 0 0 29px}
.nl-btn{left:677px;top:3062px;width:140px;height:51px;background:var(--white);color:var(--slate)}

/* footer */
.footer{left:0;top:3168px;width:1200px;height:519px;background:var(--footer)}
.foot-brand{left:0;top:3285px;width:1200px;display:flex;justify-content:center;align-items:center;gap:22px}
.foot-brand .brand-mark{width:70px;height:70px}
.foot-brand .brand-name{font-size:60px;color:#8d9799;letter-spacing:3px}
.ico{width:46px;height:46px;border-radius:50%;background:var(--green);display:flex;align-items:center;justify-content:center}
.foot-text{color:var(--white);font-size:15px;line-height:24px}
.foot-label{font-family:"Roboto",sans-serif;font-weight:700;font-size:19px;color:var(--white)}
.copyright{left:0;top:3524px;width:1200px;text-align:center;font-size:15px;color:var(--white)}
.copyright .link{color:var(--green);text-decoration:underline}
.social{width:36px;height:36px;border-radius:50%}
</style>
</head>
<body>

<header class="site-header abs">
  <div class="brand abs"><span class="brand-mark"></span><span class="brand-name">VERDELL TREE CARE</span></div>
  <nav class="nav abs">
    <span style="left:697px">Home</span>
    <span style="left:770px">About</span>
    <span style="left:843px">Services</span>
    <span style="left:934px">blog</span>
    <span style="left:995px">Contact</span>
  </nav>
</header>

<section class="hero abs" role="img" aria-label="Gloved hands planting a sapling in a forest floor"></section>
<h1 class="hero-title abs">VERDELL TREE <span class="mark">CARE</span></h1>
<p class="hero-sub abs">LOREM IPSUM DOLOR SIT AMET, CONSECTETUR</p>
<a class="btn btn-shop abs">Shop Now</a>
<a class="btn btn-explore abs">Explore Tea Sets</a>

<!-- services -->
<h2 class="sec-title abs" style="left:119px;top:766px">OUR SERV<span class="mark">ICES</span></h2>
<div class="arrow arrow-prev abs"><svg width="12" height="12" viewBox="0 0 12 12"><path d="M8 2 4 6l4 4" fill="none" stroke="#fff" stroke-width="1.8"/></svg></div>
<div class="arrow arrow-next abs"><svg width="12" height="12" viewBox="0 0 12 12"><path d="M4 2l4 4-4 4" fill="none" stroke="#333" stroke-width="1.8"/></svg></div>

<div class="card card-photo abs" style="left:120px;top:870px;width:288px;height:359px;background:linear-gradient(180deg,#5d7446,#2e4424 70%,#1d2a18)" role="img" aria-label="Gardener in gloves pruning shrubs"><span class="card-label">Provides Tree Pruning</span></div>
<div class="card-feature abs">
  <div class="img" role="img" aria-label="Arborist cutting a tree trunk with a chainsaw"></div>
  <h3>Tree Removal</h3>
  <p>Lorem ipsum dolor sit amet, consectetur adipiscing elit, sed do eiusmod tempor incididunt ut labore et dolore magna aliqua.</p>
  <span class="more">Learn More <svg width="11" height="11" viewBox="0 0 12 12"><circle cx="6" cy="6" r="6" fill="#3c5a3c"/><path d="M5 3.5 7.5 6 5 8.5" fill="none" stroke="#fff" stroke-width="1.5"/></svg></span>
</div>
<div class="card card-photo abs" style="left:789px;top:870px;width:288px;height:359px;background:linear-gradient(180deg,#6a5a48,#3f3226 60%,#2a2119)" role="img" aria-label="Hands cupping a seedling in soil"><span class="card-label">Tree Preservation</span></div>
<div class="card card-photo abs" style="left:1118px;top:867px;width:120px;height:359px;background:linear-gradient(180deg,#7a7a5c,#4c4a36)" role="img" aria-label="Hands on a tree trunk"><span class="card-label">Emergency</span></div>

<!-- what we do -->
<div class="blob abs" style="left:89px;top:1360px;width:524px;height:344px;background:radial-gradient(ellipse at 50% 55%,#5b4631,#3b3024 60%,#23201a)" role="img" aria-label="Workers planting young trees in dark soil"></div>
<h2 class="sec-title abs" style="left:637px;top:1359px">WHAT W<span class="mark">E DO</span></h2>
<p class="body-copy abs" style="left:641px;top:1426px;width:455px">At Verdell Tree Care, we are more than just a tree service company, we are stewards of our beautiful trees. With a passion deeply rooted in arboriculture, we embark on a mission to promote the health, beauty, and safety of your trees and landscapes. Whether it's expert tree trimming to enhance aesthetics, meticulous tree removal to mitigate hazards, or comprehensive tree health assessments to ensure safety, we approach each task with unwavering dedication and attention to detail.</p>
<a class="btn btn-slate abs" style="left:640px;top:1690px;width:143px;height:51px">Learn More</a>

<!-- why choose us -->
<h2 class="sec-title abs" style="left:112px;top:1840px">WHY CHOO<span class="mark">SE US</span></h2>
<ul class="checklist abs" style="left:112px;top:1910px">
  <li><svg width="13" height="13" viewBox="0 0 14 14"><circle cx="7" cy="7" r="7" fill="var(--green)"/><path d="M4 7.2 6.2 9.3 10 5" fill="none" stroke="#fff" stroke-width="1.7"/></svg>Licensed and Insured</li>
  <li><svg width="13" height="13" viewBox="0 0 14 14"><circle cx="7" cy="7" r="7" fill="var(--green)"/><path d="M4 7.2 6.2 9.3 10 5" fill="none" stroke="#fff" stroke-width="1.7"/></svg>24-Hours Emergency Services</li>
  <li><svg width="13" height="13" viewBox="0 0 14 14"><circle cx="7" cy="7" r="7" fill="var(--green)"/><path d="M4 7.2 6.2 9.3 10 5" fill="none" stroke="#fff" stroke-width="1.7"/></svg>Locally Owned &amp; Operated Professional Work</li>
  <li><svg width="13" height="13" viewBox="0 0 14 14"><circle cx="7" cy="7" r="7" fill="var(--green)"/><path d="M4 7.2 6.2 9.3 10 5" fill="none" stroke="#fff" stroke-width="1.7"/></svg>Safety is Our No.1 Priority - Free Estimates</li>
  <li><svg width="13" height="13" viewBox="0 0 14 14"><circle cx="7" cy="7" r="7" fill="var(--green)"/><path d="M4 7.2 6.2 9.3 10 5" fill="none" stroke="#fff" stroke-width="1.7"/></svg>Licensed Arborist on Staff</li>
</ul>
<a class="btn btn-slate abs" style="left:112px;top:2119px;width:143px;height:52px">Learn More</a>
<div class="blob abs" style="left:591px;top:1833px;width:526px;height:344px;background:radial-gradient(ellipse at 45% 50%,#5e6b3e,#3d4a2a 60%,#2b3420)" role="img" aria-label="Hand resting on a moss-covered tree trunk"></div>

<!-- testimonials -->
<section class="testimonials abs"></section>
<h2 class="sec-title abs" style="left:348px;top:2369px">CLIENTS TE<span class="mark">STIMONIALS</span></h2>
<div class="avatar abs" style="left:524px;top:2502px;width:44px;height:44px;background:#b59a84" role="img" aria-label="Client portrait"></div>
<div class="avatar abs" style="left:620px;top:2502px;width:44px;height:44px;background:#a88672" role="img" aria-label="Client portrait"></div>
<div class="avatar abs" style="left:562px;top:2492px;width:64px;height:64px;background:#8a9299;border-color:#9fb7c9" role="img" aria-label="Client portrait"></div>
<p class="quote abs">Lorem ipsum dolor sit amet, consectetur adipiscing elit, sed do eiusmod tempor incididunt ut labore et dolore magna aliqua. Quis ipsum suspendisse ultrices gravida. Risus commodo viverra maecenas accumsan lacus vel facilisis. Lorem ipsum dolor sit amet, consectetur adipiscing elit, sed do eiusmod tempor incididunt ut labore et dolore magna aliqua. Quis ipsum suspendisse ultrices gravida.</p>
<p class="client-name abs">MARTIN CALDO</p>
<p class="client-role abs">Lorem Ipsum</p>
<svg class="abs" style="left:570px;top:2808px" width="60" height="12" viewBox="0 0 60 12">
  <circle cx="6" cy="6" r="4.5" fill="#3f4f3f"/><circle cx="18" cy="6" r="4.5" fill="#3f4f3f"/><circle cx="30" cy="6" r="4" fill="none" stroke="#3f4f3f" stroke-width="1.2"/><circle cx="42" cy="6" r="4.5" fill="#3f4f3f"/><circle cx="54" cy="6" r="4.5" fill="#3f4f3f"/>
</svg>

<!-- newsletter -->
<section class="newsletter abs"></section>
<h2 class="nl-title abs">SIGNING UP FOR NEWSLETTERS</h2>
<p class="nl-text abs">Lorem ipsum dolor sit amet, consectetur adipiscing elit, sed do eiusmod tempor</p>
<div class="nl-input abs">Your Email Address</div>
<a class="btn nl-btn abs">Sign Up</a>

<!-- footer -->
<footer class="footer abs"></footer>
<div class="foot-brand abs"><span class="brand-mark"></span><span class="brand-name">VERDELL TREE CARE</span></div>

<div class="ico abs" style="left:195px;top:3428px"><svg width="16" height="20" viewBox="0 0 16 20"><path d="M8 0a7 7 0 0 0-7 7c0 5 7 13 7 13s7-8 7-13a7 7 0 0 0-7-7z" fill="#fff"/><circle cx="8" cy="7" r="2.6" fill="var(--green)"/></svg></div>
<p class="foot-text abs" style="left:266px;top:3425px;width:215px">112/b Verdell Tree Care. sit amet, consectetur adipiscing</p>

<div class="ico abs" style="left:511px;top:3431px"><svg width="20" height="20" viewBox="0 0 24 24"><path d="M6.6 10.8a15 15 0 0 0 6.6 6.6l2.2-2.2a1 1 0 0 1 1-.25 11.4 11.4 0 0 0 3.6.57 1 1 0 0 1 1 1V20a1 1 0 0 1-1 1A17 17 0 0 1 3 4a1 1 0 0 1 1-1h3.5a1 1 0 0 1 1 1c0 1.25.2 2.45.57 3.6a1 1 0 0 1-.25 1z" fill="#fff"/></svg></div>
<p class="foot-label abs" style="left:576px;top:3423px">PHONE</p>
<p class="foot-label abs" style="left:579px;top:3450px;font-weight:500;font-size:21px">(555) 214-8830</p>

<div class="ico abs" style="left:745px;top:3431px"><svg width="20" height="16" viewBox="0 0 20 16"><rect x="0" y="0" width="20" height="16" rx="2" fill="#fff"/><path d="M1 2l9 7 9-7" fill="none" stroke="var(--green)" stroke-width="1.8"/></svg></div>
<p class="foot-label abs" style="left:811px;top:3425px">EMAIL</p>
<p class="foot-text abs" style="left:813px;top:3452px;font-size:16px">info@verdelltreecare.com</p>

<p class="copyright abs">Copyright© 2024 &nbsp;<span class="link">Verdell Tree Care</span>&nbsp; | &nbsp;All Rights Reserved</p>
<div class="social abs" style="left:560px;top:3580px;background:var(--green)" role="img" aria-label="Social profile link"></div>
<div class="social abs" style="left:604px;top:3580px;background:var(--white)" role="img" aria-label="Social profile link"></div>

</body>
</html>
```